Volbrey Inc Business Card

Looking to get an updated business card for a Contract Machining company (www.volbreyinc.example) - looking for a clean design the portrays the technical nature of the business - colors can follow the website design and be in any combination that makes sense (red black, white, metallic or silver) - logos attached for use also. Would like space for: Name, title, business phone (555 214-3086), cell phone , website (www.volbreyinc.example) - possibly QR code could be integrated for website (designer choice), business address - 418 Harlow Bend, Larkwood, OH 44871 (cards will be for 4 employees, I will either need to modify a template or I can provide individual information)
Target Market(s)
Aerospace, defense and medical device manufacturing companies that need machining
Industry/Entity Type
Machining for aerospace, defense, medical
Contact Information for Business Card
Name, Title, Business Phone, Cell Phone, email, business website and business address
Look and feel

```html
<!DOCTYPE html>
<html lang="en">
<head>
<meta charset="utf-8">
<title>Volbrey Inc Business Card</title>
<link href="https://fonts.googleapis.com/css2?family=Poppins:wght@400;700&display=swap" rel="stylesheet">
<style>
  :root {
    --bg: #3a3a3a;
    --red: #b01e23;
    --red-bright: #d81d23;
    --red-deep: #6a080b;
    --black: #1d1d1d;
    --white: #ffffff;
    --grey-line: #5a5a5a;
  }
  * { box-sizing: border-box; margin: 0; padding: 0; }
  html, body { width: 1200px; height: 689px; overflow: hidden; }
  body {
    background: var(--bg);
    font-family: "Poppins", sans-serif;
    position: relative;
  }
  .card {
    position: absolute;
    top: 190px;
    width: 540px;
    height: 309px;
    border-radius: 18px;
    overflow: hidden;
  }
  /* Front */
  .card-front { left: 40px; background: var(--red); }
  .front-decor {
    position: absolute;
    left: 0; top: 0;
    width: 330px; height: 309px;
    background: linear-gradient(160deg, var(--red-bright) 0%, var(--red) 40%, var(--red-deep) 100%);
    clip-path: polygon(0 0, 62% 0, 100% 100%, 0 100%);
  }
  .front-wordmark {
    position: absolute;
    left: 250px; top: 128px;
    color: var(--white);
    font-weight: 700;
    font-size: 34px;
    letter-spacing: 1px;
    white-space: nowrap;
  }
  /* Back */
  .card-back { left: 620px; background: var(--black); }
  .brand-block {
    position: absolute;
    left: 34px; top: 52px;
    width: 200px;
    text-align: center;
  }
  .brand-circle {
    width: 126px; height: 126px;
    border-radius: 50%;
    background: var(--red);
    margin: 0 auto 18px;
  }
  .brand-name {
    color: var(--red);
    font-weight: 700;
    font-size: 25px;
    letter-spacing: 0.5px;
    white-space: nowrap;
  }
  .divider {
    position: absolute;
    left: 252px; top: 40px;
    width: 1px; height: 170px;
    background: var(--grey-line);
  }
  .contact {
    position: absolute;
    left: 272px; top: 44px;
    color: var(--white);
  }
  .person-name {
    color: var(--red);
    font-weight: 700;
    font-size: 17px;
    text-transform: uppercase;
    letter-spacing: 0.3px;
  }
  .person-title { font-size: 13px; margin-bottom: 12px; }
  .contact-list { list-style: none; font-size: 12.5px; line-height: 1.75; }
  .contact-list li { display: flex; align-items: center; gap: 8px; white-space: nowrap; }
  .contact-list svg { width: 13px; height: 13px; fill: var(--red); flex: none; }
  .accent { color: var(--red); }
  .address { font-size: 12.5px; line-height: 1.45; margin-top: 10px; }
  .bottom-band {
    position: absolute;
    left: 0; right: 0; bottom: 22px;
    height: 7px;
    background: var(--red);
  }
  .band-slashes {
    position: absolute;
    right: 14px; bottom: 32px;
    width: 70px; height: 14px;
  }
</style>
</head>
<body>
  <section class="card card-front">
    <div class="front-decor" role="img" aria-label="Large angular red brand decoration"></div>
    <div class="front-wordmark">VOLBREY INC.</div>
  </section>

  <section class="card card-back">
    <div class="brand-block">
      <div class="brand-circle"></div>
      <div class="brand-name">VOLBREY INC.</div>
    </div>
    <div class="divider"></div>
    <div class="contact">
      <div class="person-name">Daniel Harker</div>
      <div class="person-title">Managing Director</div>
      <ul class="contact-list">
        <li><svg viewBox="0 0 24 24"><path d="M6.6 10.8a15.1 15.1 0 0 0 6.6 6.6l2.2-2.2a1 1 0 0 1 1-.25 11.4 11.4 0 0 0 3.6.57 1 1 0 0 1 1 1V20a1 1 0 0 1-1 1A17 17 0 0 1 3 4a1 1 0 0 1 1-1h3.5a1 1 0 0 1 1 1c0 1.25.2 2.45.57 3.57a1 1 0 0 1-.25 1z"/></svg><span>555 214-3086</span></li>
        <li><svg viewBox="0 0 24 24"><path d="M7 1h10a2 2 0 0 1 2 2v18a2 2 0 0 1-2 2H7a2 2 0 0 1-2-2V3a2 2 0 0 1 2-2zm0 3v14h10V4zm5 15.5a1 1 0 1 0 0 2 1 1 0 0 0 0-2z"/></svg><span>555 860-4412</span></li>
        <li><svg viewBox="0 0 24 24"><path d="M2 5h20v14H2zm2 2v.5l8 5 8-5V7zm0 2.8V17h16V9.8l-8 5z"/></svg><span>info@volbreyinc.example</span></li>
        <li><svg viewBox="0 0 24 24"><path d="M12 2a10 10 0 1 0 0 20 10 10 0 0 0 0-20zm6.9 6h-3a15 15 0 0 0-1.3-3.9A8 8 0 0 1 18.9 8zM12 4c.8 1.2 1.5 2.5 1.9 4h-3.8c.4-1.5 1.1-2.8 1.9-4zM4.3 14a8 8 0 0 1 0-4h3.4a16 16 0 0 0 0 4zm.8 2h3a15 15 0 0 0 1.3 3.9A8 8 0 0 1 5.1 16zm3-8h-3a8 8 0 0 1 4.3-3.9A15 15 0 0 0 8.1 8zM12 20c-.8-1.2-1.5-2.5-1.9-4h3.8c-.4 1.5-1.1 2.8-1.9 4zm2.3-6H9.7a14 14 0 0 1 0-4h4.6a14 14 0 0 1 0 4zm.3 5.9a15 15 0 0 0 1.3-3.9h3a8 8 0 0 1-4.3 3.9zm1.7-5.9a16 16 0 0 0 0-4h3.4a8 8 0 0 1 0 4z"/></svg><span>www.<span class="accent">volbreyinc</span>.example</span></li>
      </ul>
      <div class="address">418 Harlow Bend,<br>Larkwood, OH 44871</div>
    </div>
    <svg class="band-slashes" viewBox="0 0 70 14">
      <polygon points="6,14 12,0 18,0 12,14" fill="#b01e23"/>
      <polygon points="22,14 28,0 34,0 28,14" fill="#b01e23"/>
      <polygon points="38,14 44,0 50,0 44,14" fill="#b01e23"/>
      <polygon points="54,14 60,0 70,0 70,14" fill="#b01e23"/>
    </svg>
    <div class="bottom-band"></div>
  </section>
</body>
</html>
```